new construction company branding

branding

Can I have a banner made so I can hang it as 1) branding my jobsite 2) advertisement

Target Market(s)

Commercial

Industry/Entity Type

Construction Trade

Font styles to use
Other font styles liked:
• Cinzel bold

Colors
EB3D1F
EC4F4E
F09395
F8D3D4
FCEDEE

Requirements
Must have
• Bright colors for advertisement
Nice to have
• 36”x48” canvas
Should not have
• To busy

```html
<!DOCTYPE html>
<html lang="en">
<head>
<meta charset="utf-8">
<title>Keystone Build LLC – Jobsite Banner</title>
<link href="https://fonts.googleapis.com/css2?family=Cinzel:wght@700&family=Montserrat:wght@500;600;700&display=swap" rel="stylesheet">
<style>
  :root {
    --brand-red: #e10d12;
    --brand-red-soft: #ec4f4e;
    --charcoal: #414141;
    --ink: #373737;
    --paper: #ffffff;
    --logo-grey: #dcdcdc;
  }
  html, body {
    margin: 0;
    padding: 0;
    width: 1200px;
    height: 720px;
    overflow: hidden;
    background: var(--paper);
  }
  .banner { display: block; width: 1200px; height: 720px; }
  .sans { font-family: "Montserrat", Arial, sans-serif; }
  .serif { font-family: "Cinzel", Georgia, serif; font-weight: 700; }
  .headline-red { fill: var(--brand-red); font-weight: 700; }
  .headline-dark { fill: var(--ink); font-weight: 600; }
  .trade { fill: var(--ink); font-weight: 600; }
  .credential { fill: var(--brand-red); font-weight: 600; }
  .phone-number { fill: var(--paper); font-weight: 700; }
  .web-address { fill: var(--paper); font-weight: 600; }
  .company-name { fill: var(--logo-grey); }
  .company-tagline { fill: var(--brand-red); }
  .red-shape { fill: var(--brand-red); }
  .dark-shape { fill: var(--charcoal); }
</style>
</head>
<body>
<svg class="banner" viewBox="0 0 1200 720" xmlns="http://www.w3.org/2000/svg" role="img" aria-label="Keystone Build LLC general contractor banner">
  <defs>
    <linearGradient id="texture-fade" x1="0" y1="0" x2="1" y2="0">
      <stop offset="0" stop-color="#ffffff" stop-opacity="0"/>
      <stop offset="0.45" stop-color="#eeeeee"/>
      <stop offset="1" stop-color="#c9c9c9"/>
    </linearGradient>
    <linearGradient id="roof-fill" x1="0" y1="1" x2="1" y2="0">
      <stop offset="0" stop-color="#e10d12"/>
      <stop offset="1" stop-color="#ec4f4e"/>
    </linearGradient>
  </defs>

  <rect class="background" width="1200" height="720" fill="var(--paper)"/>

  <!-- faceted texture area, top right -->
  <rect class="texture-panel" x="740" y="0" width="460" height="430" fill="url(#texture-fade)"
        role="img" aria-label="Soft grey geometric triangle texture"/>

  <!-- headline -->
  <text class="sans headline-red" x="23" y="108" font-size="92" textLength="1114" lengthAdjust="spacingAndGlyphs">TOGETHER ACHIEVING</text>
  <text class="sans headline-dark" x="24" y="188" font-size="76" textLength="680" lengthAdjust="spacingAndGlyphs">COMMON GOALS</text>

  <!-- divider -->
  <line class="divider" x1="33" y1="237" x2="661" y2="237" stroke="var(--brand-red)" stroke-width="1.5"/>
  <polygon class="divider-mark dark-shape" points="333,218 397,218 361,250 297,250"/>

  <!-- trade and credentials -->
  <text class="sans trade" x="25" y="312" font-size="44" textLength="550" lengthAdjust="spacingAndGlyphs">GENERAL CONTRACTOR</text>
  <text class="sans credential" x="23" y="366" font-size="37" textLength="164" lengthAdjust="spacingAndGlyphs">#2048317</text>
  <text class="sans credential" x="23" y="408" font-size="37" textLength="284" lengthAdjust="spacingAndGlyphs">Bonded/insured</text>

  <!-- house illustration area -->
  <rect class="house-illustration" x="545" y="340" width="345" height="380" fill="url(#roof-fill)"
        role="img" aria-label="Red roofline and chimney house illustration with swoosh"/>

  <!-- phone band -->
  <rect class="phone-band red-shape" x="0" y="576" width="560" height="78"/>

  <!-- website band -->
  <polygon class="web-band dark-shape" points="0,654 390,654 346,705 0,705"/>

  <!-- dark curved corner -->
  <path class="corner-white-edge" d="M630,720 C713,560 893,398 1200,342 L1200,352 C900,405 720,562 640,720 Z" fill="var(--paper)"/>
  <path class="corner dark-shape" d="M637,720 C720,560 900,400 1200,351 L1200,720 Z"/>

  <!-- phone -->
  <g class="phone-icon" fill="none" stroke="var(--paper)" stroke-width="3">
    <rect x="23" y="592" width="24" height="46" rx="3"/>
    <line x1="23" y1="599" x2="47" y2="599"/>
    <line x1="23" y1="631" x2="47" y2="631"/>
  </g>
  <text class="sans phone-number" x="63" y="639" font-size="66" textLength="473" lengthAdjust="spacingAndGlyphs">123-4567-890</text>

  <!-- website -->
  <g class="globe-icon" fill="none" stroke="var(--paper)" stroke-width="1.5">
    <circle cx="34" cy="678" r="8"/>
    <ellipse cx="34" cy="678" rx="3.5" ry="8"/>
    <line x1="26" y1="678" x2="42" y2="678"/>
  </g>
  <text class="sans web-address" x="51" y="686" font-size="23" textLength="300" lengthAdjust="spacingAndGlyphs">www.yourwebsiet.com</text>

  <!-- company mark placeholder and name -->
  <circle class="company-mark" cx="925" cy="528" r="42" fill="var(--logo-grey)"
          role="img" aria-label="Company logo mark placeholder"/>
  <text class="serif company-name" x="950" y="617" font-size="30" text-anchor="middle" textLength="360" lengthAdjust="spacingAndGlyphs">KEYSTONE BUILD LLC</text>
  <text class="serif company-tagline" x="953" y="658" font-size="24" text-anchor="middle" textLength="396" lengthAdjust="spacingAndGlyphs">GENERAL CONTRACTOR</text>
</svg>
</body>
</html>
```